Broschüre im Bereich Steuerberatung
Zielgruppe
Steuerberatung
Aufgabenstellung
Die Seite 1 wäre eigentlich fertig, natürlich bin ich offen für Optimierungen. Die weiteren fünf Seiten gilt es noch zu gestalten:
Seite 1
Buchhaltung
Lohnwesen
Steuern
Firmengründung
Kontakt

```html
<!DOCTYPE html>
<html lang="de">
<head>
<meta charset="utf-8">
<title>Brunner Treuhand – Broschüre</title>
<link rel="stylesheet" href="https://fonts.googleapis.com/css2?family=Bodoni+Moda:wght@400;500&family=Italiana&family=Poppins:wght@300;400;500;600&display=swap">
<style>
:root{
  --backdrop:#69a6e4;
  --paper:#ffffff;
  --orange:#f26722;
  --navy:#1d4b8f;
  --ink:#1e1e1e;
  --body:#2b2b2b;
  --line:#222;
}
*{margin:0;padding:0;box-sizing:border-box}
html,body{width:1200px;height:2360px;overflow:hidden;background:var(--backdrop)}
body{position:relative;font-family:'Poppins',sans-serif;color:var(--body)}
.page{position:absolute;width:488px;height:690px;background:var(--paper);overflow:hidden}
.p1{left:99px;top:118px}.p2{left:617px;top:118px}
.p3{left:99px;top:839px}.p4{left:617px;top:839px}
.p5{left:99px;top:1551px}.p6{left:617px;top:1551px}
.abs{position:absolute}
.photo{position:absolute}
.url{position:absolute;left:26px;top:642px;font-size:13.5px;letter-spacing:.6px;color:var(--ink);line-height:1}
.rule{position:absolute;left:196px;right:0;top:650px;height:1px;background:var(--line)}
/* cover */
.brand-line{position:absolute;left:0;right:0;top:40px;display:flex;justify-content:center;align-items:center;gap:10px}
.brand-square{width:12px;height:12px;background:var(--navy)}
.brand-name{font-family:'Poppins',sans-serif;font-weight:500;font-size:19px;letter-spacing:1px;color:var(--navy);line-height:1}
.cover-brand{position:absolute;left:0;right:0;top:470px;text-align:center;color:#fff;font-family:'Bodoni Moda',serif;font-size:80px;letter-spacing:-1px;line-height:1}
.cover-sub{position:absolute;left:0;right:0;top:573px;text-align:center;color:#fff;font-size:17px;letter-spacing:1.5px}
.cover-url{position:absolute;left:0;right:0;top:642px;text-align:center;font-size:13.5px;letter-spacing:.6px;color:var(--ink)}
/* intro page */
.intro-title{position:absolute;left:26px;top:36px;font-family:'Italiana',serif;font-weight:400;font-size:25px;line-height:1.15;color:var(--ink)}
.kicker{font-size:10.5px;font-weight:500;line-height:1.3;color:var(--ink);margin-bottom:8px;text-transform:uppercase}
.txt{font-size:8.6px;line-height:1.72;text-align:justify;hyphens:auto}
.svc-head{font-family:'Italiana',serif;font-size:12px;letter-spacing:.5px;margin-bottom:5px;text-transform:uppercase;color:var(--ink)}
.orange-col{position:absolute;left:231px;top:318px;width:257px;height:372px;background:var(--orange);color:#fff}
.orange-col .svc-head{color:#fff}
/* service pages */
.motto{position:absolute;left:0;right:0;top:24px;text-align:center;font-family:'Italiana',serif;font-size:20px;letter-spacing:6px;color:var(--ink)}
.motto.light{color:#fff}
.label{position:absolute;left:118px;top:276px;width:257px;height:57px;background:var(--orange);color:#fff;text-align:center;font-family:'Italiana',serif;font-size:36px;line-height:57px}
.headline{position:absolute;left:20px;right:20px;text-align:center;font-size:11.5px;font-weight:600;color:var(--ink);line-height:1.3}
.subline{position:absolute;left:20px;right:20px;text-align:center;font-size:9px;color:var(--ink)}
.col{position:absolute;width:232px}
.bold-note{font-size:8.6px;line-height:1.72;font-weight:600;text-align:justify;color:var(--ink)}
.arrow{position:absolute;width:24px;height:24px}
.center-txt{position:absolute;left:30px;right:30px;text-align:center;font-size:8px;line-height:1.85}
.contact{position:absolute;top:630px;font-size:8.6px;font-weight:600;line-height:1.4;color:var(--ink)}
</style>
</head>
<body>

<section class="page p1">
  <div class="brand-line"><span class="brand-square"></span><span class="brand-name">Brunner Treuhand</span></div>
  <div class="photo" role="img" aria-label="Stadtstrasse mit Hochhäusern und Bäumen im Abendlicht" style="left:0;top:91px;width:488px;height:524px;background:linear-gradient(100deg,#8a6f74 0%,#9d8a95 30%,#6f7f95 55%,#4a5a78 80%,#3c4b68 100%)"></div>
  <div class="photo" aria-hidden="true" style="left:0;top:360px;width:488px;height:255px;background:linear-gradient(180deg,rgba(70,90,60,0) 0%,rgba(70,90,60,.55) 60%,rgba(120,110,110,.6) 100%)"></div>
  <div class="cover-brand">BRUNNER</div>
  <div class="cover-sub">TREUHAND CONSULTING</div>
  <div class="cover-url">brunnertreuhand.ch</div>
</section>

<section class="page p2">
  <h1 class="intro-title">Zuverlässig und<br>partnerschaftlich:</h1>
  <div class="abs" style="left:26px;top:122px;width:192px">
    <div class="kicker">Ihre massgeschneiderten<br>Treuhand-Lösungen</div>
    <p class="txt">Sie möchten Ihre Steuern, Ihre Buchhaltung oder Ihr Lohnwesen in verlässliche Hände geben? Sie legen Wert auf eine persönliche Betreuung mit gleichbleibendem Ansprechpartner, auf individuelle Strategien und auf ein angenehmes Miteinander?</p>
    <p class="txt" style="margin-top:10px;text-align:left">Dann freue ich mich auf Ihre Kontaktaufnahme</p>
  </div>
  <div class="photo" role="img" aria-label="Porträt der Treuhänderin vor hellem Hintergrund" style="left:231px;top:0;width:257px;height:318px;background:linear-gradient(160deg,#e2e4e6 0%,#d6d3d0 45%,#c89579 70%,#2b2b2e 100%)"></div>
  <div class="orange-col">
    <div class="abs" style="left:26px;top:42px;width:208px">
      <div class="svc-head">Steuererklärung</div>
      <p class="txt">Jeder möchte seine Steuerlast optimieren, nur wenige setzen sich aktiv damit auseinander. Denn das kostet Zeit und verlangt nach umfangreichem Wissen. Vertrauen Sie mir Ihre Steuererklärungen an – und holen Sie sich zurück, was Ihnen zusteht.</p>
    </div>
    <div class="abs" style="left:26px;top:187px;width:208px">
      <div class="svc-head">Firmengründung</div>
      <p class="txt">Gründen Sie Ihre Schweizer Gesellschaft schnell und sicher. Mit meiner langjährigen Erfahrung, meinem Wissen und meiner Zusammenarbeit mit einem versierten Notar unterstütze ich Sie zuverlässig – auch über Ihre Gründung hinaus.</p>
    </div>
  </div>
  <div class="abs" style="left:26px;top:363px;width:192px">
    <div class="svc-head">Buchhaltung</div>
    <p class="txt">Buchhaltung ist komplex und aufwendig – das kostet Unternehmer viel Zeit, die sie anderswo wertschöpfend einsetzen könnten. Mithilfe moderner Hilfsmittel und bewährter Prozesse entlaste ich Sie zuverlässig und zum Fixpreis.</p>
  </div>
  <div class="abs" style="left:26px;top:506px;width:192px">
    <div class="svc-head">Lohnwesen</div>
    <p class="txt">Entscheiden Sie selbst, in welcher Form Sie auf meine Expertise zugreifen, um sich beim Thema Lohnbuchhaltung zu entlasten.</p>
  </div>
  <div class="url">brunnertreuhand.ch</div>
  <div class="rule"></div>
</section>

<section class="page p3">
  <div class="photo" role="img" aria-label="Treuhänderin in gestreifter Bluse vor grauer Wand" style="left:0;top:0;width:488px;height:317px;background:linear-gradient(180deg,#d4d4d4 0%,#c9c9c9 50%,#b9bcc4 100%)"></div>
  <div class="motto light">ADDITION.SUBTRAKTION.ERFOLG.</div>
  <div class="label">Buchhaltung</div>
  <div class="headline" style="top:354px">Buchhaltung kostet Sie viel Zeit – ich gebe sie Ihnen zurück</div>
  <div class="subline" style="top:375px">Ich übernehme Ihre Buchhaltung – akribisch, verlässlich, verantwortungsvoll</div>
  <div class="col" style="left:26px;top:413px">
    <p class="txt">Unternehmer zählen die Buchhaltung in der Regel nicht zu ihren Leidenschaften.</p>
    <p class="txt" style="margin-top:8px">Und dennoch ist eine ordentliche Buchhaltung das Rückgrat eines jeden erfolgreichen Betriebs. Es ergibt also durchaus Sinn, hierfür ausreichend Ressourcen bereitzustellen – jedoch nicht die eigenen.</p>
    <p class="txt" style="margin-top:8px">Wenn Sie selbst oder Ihre Mitarbeiter sich um dieses komplexe „Pflichtthema“ kümmern, bleiben andere, wertschöpfende Tätigkeiten auf der Strecke: neue Kunden akquirieren, Produkte weiterentwickeln, Services ausbauen usw.</p>
  </div>
  <div class="col" style="left:272px;top:413px;width:194px">
    <p class="txt">Die Folge: Es kommt zu unnötigem Mehraufwand und die Entwicklung Ihres Unternehmens schreitet lang samer voran als geplant.</p>
    <p class="txt" style="margin-top:8px">Beides ist unschön – und beides lässt sich leicht vermeiden. Nutzen Sie Ihre wertvolle Zeit lieber gewinnbringend und überlassen Sie Ihre Buchhaltung einem Profi.</p>
    <p class="txt" style="margin-top:8px">Mit viel Erfahrung, Wissen und Leidenschaft kümmere ich mich um Ihre Geschäftsvorfälle, während Ihr Team und Sie sich auf Ihre Kerntätigkeit fokussieren.</p>
  </div>
  <div class="url">brunnertreuhand.ch</div>
  <div class="rule"></div>
</section>

<section class="page p4">
  <div class="photo" role="img" aria-label="Treuhänderin in gestreifter Bluse im hellen Raum" style="left:0;top:0;width:488px;height:317px;background:linear-gradient(90deg,#f3f3f3 0%,#ececec 55%,#d9cfc8 80%,#c8c9d0 100%)"></div>
  <div class="motto">EINFACH.MEHR.LOHN.</div>
  <div class="label">Lohnwesen</div>
  <div class="headline" style="top:354px">Lohnbuchhaltung ohne Stress: So gewinnen Sie mehr Zeit</div>
  <div class="subline" style="top:375px">Ich erledige Ihr Lohnwesen – präzise, sicher, zuverlässig</div>
  <div class="col" style="left:26px;top:413px;width:218px">
    <p class="txt">Sicherlich stimmen Sie mir zu, wenn ich das Personalwesen und die Saläradministration zu den sensiblen Bereichen Ihres Unternehmens zähle. Schliesslich erwarten Ihre Mitarbeiter, dass ihre Gehälter pünktlich auf dem Konto eingehen.</p>
    <p class="txt" style="margin-top:8px">Doch die Lohnbuchhaltung ist komplex und daher zeitaufwändig – sie bindet wertvolle Ressourcen, die Ihnen für andere, wertschöpfende Tätigkeiten fehlen.</p>
    <p class="txt" style="margin-top:8px">Holen Sie sich die Zeit zurück und legen Sie Ihre Lohnbuchhaltung in meine Hände. Dabei haben Sie die Wahl zwischen Optimierung und Outsourcing:</p>
  </div>
  <svg class="arrow" style="left:260px;top:412px" viewBox="0 0 24 24" aria-hidden="true"><circle cx="12" cy="12" r="12" fill="var(--orange)"/><path d="M6 12h11M12.5 7.5 17 12l-4.5 4.5" stroke="#fff" stroke-width="1.8" fill="none" stroke-linecap="round" stroke-linejoin="round"/></svg>
  <svg class="arrow" style="left:260px;top:515px" viewBox="0 0 24 24" aria-hidden="true"><circle cx="12" cy="12" r="12" fill="var(--orange)"/><path d="M6 12h11M12.5 7.5 17 12l-4.5 4.5" stroke="#fff" stroke-width="1.8" fill="none" stroke-linecap="round" stroke-linejoin="round"/></svg>
  <div class="col" style="left:302px;top:413px;width:165px">
    <p class="bold-note">Sie übernehmen die vorbereitenden Arbeiten, während ich mich um die Umsetzung kümmere. So optimieren wir gemeinsam Ihre Vorgänge und entlasten Ihre interne Buchhaltung.</p>
  </div>
  <div class="col" style="left:302px;top:516px;width:165px">
    <p class="bold-note">Sie lagern Ihre Lohnbuchhaltung an mich aus. Insbesondere kleine und mittlere Unternehmen profitieren vom Outsourcing immens, da sie sich von diesem Thema komplett befreien.</p>
  </div>
  <div class="url">brunnertreuhand.ch</div>
  <div class="rule"></div>
</section>

<section class="page p5">
  <div class="photo" role="img" aria-label="Moderne Glasfassade mit grünen Bäumen" style="left:0;top:0;width:488px;height:317px;background:linear-gradient(135deg,#e9f1ee 0%,#a9cfc6 30%,#3f8c73 55%,#2d6e4c 75%,#8fb83a 100%)"></div>
  <div class="motto">SICHERHEIT.EFFIZIENZ.</div>
  <div class="label">Steuern</div>
  <div class="headline" style="top:358px">Professionell und transparent:<br>Ihre Steuererklärung und Steuerberatung</div>
  <div class="subline" style="top:394px">Ich kümmere mich persönlich um Ihre Steuerangelegenheiten</div>
  <p class="center-txt" style="top:424px">Steuern sind ein sensibles Thema – schliesslich geht es um Ihr Geld. Setzen Sie gleich auf professionelle Unterstützung: Vermeiden Sie teure Fehler, sparen Sie viel Zeit und schonen Sie Ihre Nerven.</p>
  <div class="headline" style="top:485px">Steuerklärung ausfüllen für Privatpersonen</div>
  <p class="center-txt" style="top:520px">Weshalb ich mir viel Zeit für Sie nehme und Sie individuell betreue? Weil wir mit Konzepten „von der Stange“ bei Ihrer Steuererklärung nicht weit kommen.</p>
  <p class="center-txt" style="top:566px">Hingegen habe ich die Abläufe rund um Ihre Steuerberatung standardisiert – um es Ihnen einfach zu machen: Wir tauschen uns per E-Mail, Telefon, Videocall oder per Post aus. So erhalten Sie schnelle Ergebnisse und sparen sich Weg und Kosten für einen persönlichen Termin.</p>
  <div class="url">brunnertreuhand.ch</div>
  <div class="rule"></div>
</section>

<section class="page p6">
  <div class="photo" role="img" aria-label="Altstadt am See mit Holzbrücke, Turm und Bergen" style="left:0;top:0;width:488px;height:317px;background:linear-gradient(180deg,#8fb4d6 0%,#b9cbd8 30%,#8a6a4a 55%,#6d7d5a 75%,#3f7c86 100%)"></div>
  <div class="motto" style="font-size:19px;letter-spacing:4.5px">SICHER.PERSÖNLICH.ERFOLGREICH</div>
  <div class="label" style="left:84px;width:320px">Firmengründung</div>
  <div class="headline" style="top:364px">Professionelle Unternehmensgründung mit System.</div>
  <div class="subline" style="top:385px;font-size:8.6px">Brunner Treuhand - Ihr kompetenter Partner.</div>
  <p class="center-txt" style="top:410px;left:30px;right:30px;font-size:7.9px;line-height:1.85">Die Gründung des eigenen Unternehmens gehört zu den emotionalsten Erlebnissen in der Karriere. Gut, wenn man hierbei einen verlässlichen Partner hat, der einen kühlen Kopf bewahrt und sich bis ins Detail mit sämtlichen Anforderungen auskennt. Schon seit mehr als 13 Jahren unterstütze ich Start-ups auf ihrem Weg an die Spitze – vom ersten Tag an rund um die Gründung und danach bei der Buchhaltung, im Lohnwesen und bei den Steuern. Was mich dabei auszeichnet, ist mein persönliches Vorgehen: Ich beschäftige mich intensiv mit den Gründern und ihrer Idee, berate sie bei der Auswahl der passenden Rechtsform und kümmere mich um sämtliche Formalitäten. Weil ich möchte, dass wir für Sie von Beginn an die richtigen Weichen stellen, gibt es bei mir keine Standardlösungen, sondern stets eine individuelle Herangehensweise. Fokussieren Sie sich auf den besten Start für Ihr Unternehmen – und überlassen Sie mir das Begleitwerk inklusive sämtlicher notarieller Beglaubigungen.</p>
  <div class="url" style="top:582px">brunnertreuhand.ch</div>
  <div class="rule" style="top:590px"></div>
  <div class="contact" style="left:35px">Montag - Freitag<br>08:00 - 12:00 Uhr<br>13:30 - 17:00 Uhr</div>
  <div class="contact" style="left:157px">+41 (0)79 000 45 67 Mobile<br><br>info@brunnertreuhand.ch</div>
  <div class="contact" style="left:305px">Brunner Treuhand Consulting GmbH<br>Seeweg 7<br>6300 Seedorf</div>
</section>

</body>
</html>
```